Marlow Vale Stud website

We would like to create a horse stud/agistment farm website similar to this websites we have attached below:
www.thornbeck.com.au
www.quillstead.com.au
www.brackley.com
www.pimsey.com.au
The main colour scheme are purple and white to align with the stable's racing colours.
We have also attach the company logo and also images of the farm and create some ideas for the website.
Many thanks for looking into this project!

```html
<!DOCTYPE html>
<html lang="en">
<head>
<meta charset="utf-8">
<title>Marlow Vale Stud</title>
<link href="https://fonts.googleapis.com/css2?family=Roboto+Slab:wght@400;700&family=Roboto:wght@400;500&display=swap" rel="stylesheet">
<style>
:root{
  --purple:#3a1641;
  --purple-dark:#2c0f33;
  --purple-foot:#43184c;
  --ink:#222;
  --muted:#555;
  --grey-bg:#ededed;
  --white:#fff;
  --line:#ddd;
}
*{box-sizing:border-box;margin:0;padding:0}
html,body{width:1200px;height:4000px;overflow:hidden}
body{position:relative;background:var(--white);font-family:"Roboto Slab",serif;color:var(--ink)}
.abs{position:absolute}
h2.section-title{position:absolute;left:0;width:1200px;text-align:center;font-size:28px;font-weight:700;color:var(--ink);text-transform:uppercase;letter-spacing:.5px}
.section-lead{position:absolute;left:300px;width:600px;text-align:center;font-size:12px;line-height:22px;color:var(--muted)}
.btn{display:inline-block;background:var(--purple);color:var(--white);font-size:11px;font-weight:700;text-transform:uppercase;padding:9px 18px;letter-spacing:.5px}

/* header */
.site-header{left:0;top:0;width:1200px;height:93px;background:var(--purple-dark)}
.brand{position:absolute;left:176px;top:28px;display:flex;align-items:center;gap:12px;color:var(--white);font-size:24px}
.brand .mark{width:34px;height:34px;border-radius:50%;border:2px solid var(--white)}
.main-nav{position:absolute;left:482px;top:38px;display:flex;gap:30px;font-family:"Roboto",sans-serif;font-size:14px;color:var(--white)}

/* hero */
.hero{left:0;top:93px;width:1200px;height:574px;background:linear-gradient(180deg,#8a8f9a 0%,#c9a574 30%,#6d7650 50%,#3d5a24 75%,#2a3c17 100%)}
.hero-title{position:absolute;left:0;top:230px;width:1200px;text-align:center;color:var(--white);font-size:58px;font-weight:700;letter-spacing:1px}
.hero .btn{position:absolute;left:545px;top:318px;border-radius:3px}
.hero-dots{position:absolute;left:582px;top:500px;display:flex;gap:5px}
.hero-dots i{width:7px;height:7px;border-radius:50%;background:var(--white);display:block}
.badge-circle{left:540px;top:627px;width:120px;height:120px;border-radius:50%;background:var(--white)}
.badge-circle span{position:absolute;left:40px;top:22px;width:40px;height:40px;border-radius:50%;border:3px solid var(--purple)}

/* services */
.service-card{top:861px;width:205px;height:320px;background:var(--white);border:1px solid var(--line)}
.service-card .photo{height:160px}
.service-card h3{font-size:15px;font-weight:400;line-height:20px;margin:20px 22px 10px;color:var(--ink)}
.service-card p{font-size:10px;line-height:16px;color:var(--muted);margin:0 22px}
.slider-arrow{top:928px}

/* video */
.video-band{left:0;top:1307px;width:1200px;height:413px;background:linear-gradient(180deg,#3a4a2e 0%,#5a7a34 50%,#4a6a24 100%)}
.video-band h2{position:absolute;top:65px;left:0;width:1200px;text-align:center;color:var(--white);font-size:28px;font-weight:700}
.video-band p{position:absolute;top:110px;left:300px;width:600px;text-align:center;color:#eee;font-size:12px;line-height:22px}
.grey-band{left:0;top:1720px;width:1200px;height:821px;background:var(--grey-bg)}
.video-frame{left:240px;top:1496px;width:716px;height:397px;background:var(--white);padding:10px;box-shadow:0 4px 14px rgba(0,0,0,.3)}
.video-frame .photo{width:100%;height:100%;background:linear-gradient(135deg,#6c8a4a 0%,#8a4a22 35%,#a45a28 55%,#5c4c3e 80%)}

/* news */
.news-card{top:2043px;width:267px;height:357px;background:var(--white);box-shadow:0 1px 4px rgba(0,0,0,.1)}
.news-card .photo{height:157px;position:relative}
.news-card .date{position:absolute;left:16px;top:14px;background:var(--purple);color:var(--white);font-size:10px;font-weight:700;padding:5px 8px}
.news-card h3{font-size:16px;font-weight:700;line-height:22px;margin:24px 24px 12px}
.news-card p{font-size:10px;line-height:17px;color:var(--muted);margin:0 24px 16px}
.news-card .more{font-size:11px;font-weight:700;text-transform:uppercase;margin:0 24px;color:var(--ink)}

/* about */
.about-photo{left:80px;top:2619px;width:563px;height:373px;background:linear-gradient(180deg,#4a7fc8 0%,#9cbde0 40%,#4a3a2c 60%,#3f7a2a 85%)}
.about-text{left:700px;top:2690px;width:340px}
.about-text h2{font-size:23px;font-weight:700;text-transform:uppercase;margin-bottom:22px}
.about-text p{font-size:11px;line-height:20px;color:var(--muted);margin-bottom:22px}
.divider{left:0;top:3080px;width:1200px;height:1px;background:var(--line)}

/* gallery */
.gallery{left:0;top:3261px;width:1200px;height:320px;display:flex;gap:6px}
.gallery div{flex:1}

/* footer */
.site-footer{left:0;top:3587px;width:1200px;height:413px;background:linear-gradient(180deg,var(--purple-foot),#32103a);color:var(--white)}
.foot-col{position:absolute;top:40px;font-size:11px;line-height:22px;color:#ddd}
.foot-col h4{font-size:16px;font-weight:700;color:var(--white);margin-bottom:6px;display:flex;align-items:center;gap:8px}
.foot-col h4 + p{margin-bottom:30px}
.foot-brand{position:absolute;left:860px;top:52px;display:flex;flex-direction:column;align-items:center;gap:10px;font-size:22px}
.foot-brand .mark{width:32px;height:32px;border-radius:50%;border:2px solid var(--white)}
.follow{position:absolute;left:860px;top:182px}
.follow h4{font-size:16px;font-weight:700;margin-bottom:18px}
.follow .icons{display:flex;gap:22px}
.follow .icons span{width:20px;height:20px;border-radius:50%;background:var(--white);display:block}
.foot-rule{position:absolute;left:173px;top:338px;width:930px;height:1px;background:rgba(255,255,255,.2)}
.copyright{position:absolute;left:0;top:362px;width:1200px;text-align:center;font-size:11px;color:#ddd}
</style>
</head>
<body>

<header class="site-header abs">
  <div class="brand"><span class="mark"></span>Marlow Vale Stud</div>
  <nav class="main-nav"><span>HOME</span><span>SERVICES</span><span>NEWS</span><span>STALLIONS</span><span>VIDEOS</span><span>GALLERY</span><span>CONTACT</span></nav>
</header>

<section class="hero abs" role="img" aria-label="Farm paddock with wooden fence at sunset">
  <h1 class="hero-title">MARLOW VALE STUD</h1>
  <span class="btn">Read more</span>
  <div class="hero-dots"><i></i><i></i><i></i><i></i></div>
</section>
<div class="badge-circle abs"><span></span></div>

<h2 class="section-title" style="top:745px">Our Services</h2>
<p class="section-lead" style="top:787px">At vero eos et accusamus et iusto odio dignissimos ducimus qui blanditiis praesentium voluptatum deleniti atque corrupti quos dolores et quas molestias excepturi sint occaecati cupiditate non provident, similique.</p>

<svg class="abs slider-arrow" style="left:130px" width="14" height="26" viewBox="0 0 14 26"><path d="M12 2 2 13l10 11" fill="none" stroke="#bbb" stroke-width="2"/></svg>
<svg class="abs slider-arrow" style="left:1046px" width="14" height="26" viewBox="0 0 14 26"><path d="M2 2l10 11L2 24" fill="none" stroke="#bbb" stroke-width="2"/></svg>

<article class="service-card abs" style="left:173px">
  <div class="photo" role="img" aria-label="Pale palomino horse standing in a paddock" style="background:linear-gradient(180deg,#5d8a3c,#c9b89a 55%,#4f7a2e)"></div>
  <h3>Silver Crest (USA)</h3>
  <p>At vero eos et accusamus et iusto odio dignissimos ducimus qui blanditiis praesent tempora omnis ducimus qui blanditiis praesent tempor nisi.</p>
</article>
<article class="service-card abs" style="left:390px">
  <div class="photo" role="img" aria-label="Bay yearling grazing near trees" style="background:linear-gradient(180deg,#8fb0c8,#4a6b32 45%,#8a4a24 70%,#4f7a2e)"></div>
  <h3>Weanling and Yearling Sales Preparation</h3>
  <p>At vero eos et accusamus et iusto odio dignissimos ducimus qui blanditiis praesent tempora omnis ducimus qui blan.</p>
</article>
<article class="service-card abs" style="left:607px">
  <div class="photo" role="img" aria-label="Mare and foal in a green field" style="background:linear-gradient(180deg,#6b8fa8,#4e7a30 40%,#7a4a2a 65%,#4f7a2e)"></div>
  <h3>Breaking/ Re-education of problem horses</h3>
  <p>At vero eos et accusamus et iusto odio dignissimos ducimus qui blanditiis praesent tempora omnis ducimus qui blan.</p>
</article>
<article class="service-card abs" style="left:824px">
  <div class="photo" role="img" aria-label="Horses grazing on a hillside" style="background:linear-gradient(180deg,#a8b8c8,#5b7a3a 45%,#4a3626 65%,#5a8a34)"></div>
  <h3>Facility hire</h3>
  <p>At vero eos et accusamus et iusto odio dignissimos ducimus qui blanditiis praesent tempora omnis ducimus qui blanditiis praesent tempor nisi.</p>
</article>

<section class="video-band abs" role="img" aria-label="Horses grazing in a paddock at dusk">
  <h2>WATCH OUR VIDEO</h2>
  <p>At vero eos et accusamus et iusto odio dignissimos ducimus qui blanditiis praesentium voluptatum deleniti atque corrupti quos dolores et quas molestias excepturi sint occaecati cupiditate non provident, similique.</p>
</section>
<div class="grey-band abs"></div>
<div class="video-frame abs">
  <div class="photo" role="img" aria-label="Bay horse standing on a farm road"></div>
  <svg class="abs" style="left:305px;top:145px" width="110" height="110" viewBox="0 0 110 110"><circle cx="55" cy="55" r="50" fill="none" stroke="#fff" stroke-width="5"/><path d="M44 32v46l36-23z" fill="#fff"/></svg>
</div>

<h2 class="section-title" style="top:1968px">Latest News</h2>

<article class="news-card abs" style="left:173px">
  <div class="photo" role="img" aria-label="Racehorse and jockey on track" style="background:linear-gradient(180deg,#b8a080,#8a5a3a 50%,#6a8a3a 80%,#c04a4a)"><span class="date">Mar 12 2019</span></div>
  <h3>Lorem ipsum dolor sit aet onsectetur adipisci</h3>
  <p>Lorem ipsum dolor sit amet, consec tetur adipiscing elit, sed do eiusmod te mpor incididunt ut labore et do</p>
  <div class="more">Read more</div>
</article>
<article class="news-card abs" style="left:467px">
  <div class="photo" role="img" aria-label="Aerial view of farm stables" style="background:linear-gradient(180deg,#9ab0c0,#5a7a3a 40%,#7a8a6a 60%,#4a6a2a)"><span class="date">Mar 12 2019</span></div>
  <h3>Lorem ipsum dolor sit aet onsectetur adipisci</h3>
  <p>Lorem ipsum dolor sit amet, consec tetur adipiscing elit, sed do eiusmod te mpor incididunt ut labore et do</p>
  <div class="more">Read more</div>
</article>
<article class="news-card abs" style="left:760px">
  <div class="photo" role="img" aria-label="Horses in a field under a cloudy sky" style="background:linear-gradient(180deg,#8a8e94,#6a7a54 45%,#4a3a2a 62%,#4f7a2e)"><span class="date">Mar 12 2019</span></div>
  <h3>Lorem ipsum dolor sit aet onsectetur adipisci</h3>
  <p>Lorem ipsum dolor sit amet, consec tetur adipiscing elit, sed do eiusmod te mpor incididunt ut labore et do</p>
  <div class="more">Read more</div>
</article>

<div class="about-photo abs" role="img" aria-label="Five young horses standing on grass under a blue sky"></div>
<div class="about-text abs">
  <h2>About Marlow Vale Stud</h2>
  <p>At vero eos et accusamus et iusto odio dignissimos ducimus blanditiis praesentium voluptatum deleniti atque corrupti quos dolores et quas molestias excepturi sint occaecati cupiditate no n provident, similique. At vero eos et accusamus et iusto odio dignissimos ducimus qui blanditiis praesentium voluptatum deleniti atque corrupti quos dolores et quas molestias excepturi sint occaecati cupiditate n provident, similique.</p>
  <span class="btn">Read more</span>
</div>

<div class="divider abs"></div>

<h2 class="section-title" style="top:3132px">Our Gallery</h2>
<p class="section-lead" style="top:3184px">At vero eos et accusamus et iusto odio dignissimos ducimus qui blanditiis praesentium voluptatum deleniti atque corrupti quos dolores et quas molestias excepturi sint occaecati cupiditate non provident, similique.</p>

<div class="gallery abs">
  <div role="img" aria-label="Aerial view of the stud buildings" style="background:linear-gradient(180deg,#6a9ad0,#b0c8d8 30%,#6a8a4a 55%,#8a7a60)"></div>
  <div role="img" aria-label="Bay horse among trees" style="background:linear-gradient(180deg,#3a5a2a,#5a8a3a 50%,#7a4a2a 70%,#4f7a2e)"></div>
  <div role="img" aria-label="Paddocks with shelters seen from above" style="background:linear-gradient(180deg,#4a7a3a,#7aaa4a 50%,#5a8a3a)"></div>
  <div role="img" aria-label="Mare with foal at a feeder" style="background:linear-gradient(180deg,#7a8a6a,#4a3a2a 45%,#6a5040 70%,#4f6a2e)"></div>
</div>

<footer class="site-footer abs">
  <div class="foot-col" style="left:173px;width:200px">
    <h4><svg width="14" height="18" viewBox="0 0 14 18"><path d="M7 1a6 6 0 0 0-6 6c0 4.5 6 10 6 10s6-5.5 6-10a6 6 0 0 0-6-6z" fill="none" stroke="#fff" stroke-width="1.4"/><circle cx="7" cy="7" r="2" fill="#fff"/></svg>Address</h4>
    <p>Marlow Vale Stud<br>Lorem ipsumdunedi 120,<br>4127 LB, Dalewick<br>Northvale</p>
    <h4><svg width="18" height="13" viewBox="0 0 18 13"><rect x="1" y="1" width="16" height="11" fill="none" stroke="#fff" stroke-width="1.4"/><path d="M1 1l8 6 8-6" fill="none" stroke="#fff" stroke-width="1.4"/></svg>Email</h4>
    <p>info@marlowvalestud.com</p>
    <h4><svg width="16" height="16" viewBox="0 0 16 16"><path d="M3 1l3 3-2 2a9 9 0 0 0 6 6l2-2 3 3-2 2C7 15 1 9 1 3z" fill="#fff"/></svg>Phone</h4>
    <p>030-5550142</p>
  </div>
  <div class="foot-col" style="left:400px">
    <h4>Links</h4>
    <p>Lorem ipsum dol adipiscin<br>Do eiusmodtem ipsum dolor<br>Consectetur adipiscin</p>
    <h4>Information</h4>
    <p>About Marlow Vale<br>Imprint<br>Contact<br>News</p>
  </div>
  <div class="foot-col" style="left:660px">
    <h4>Stallions</h4>
    <p>Lorem ipsum dolor<br>Consectetur adipiscin<br>Do eiusmodt<br>Lorem ipsum dolor<br>Consectetur adipiscin<br>Do eiusmodt<br>Lorem ipsum dolor<br>Consectetur adipiscin<br>Do eiusmodt</p>
  </div>
  <div class="foot-brand"><span class="mark"></span>Marlow Vale Stud</div>
  <div class="follow">
    <h4>Follow Us</h4>
    <div class="icons"><span></span><span></span><span></span><span></span></div>
  </div>
  <div class="foot-rule"></div>
  <p class="copyright">© 2019 Marlow Vale Stud. All rights reserved.</p>
</footer>

</body>
</html>
```